design a construction company business card

Design business card around our logo. Card must have all the typical info: name, title, address, phone, email, business name, etc. Somewhere on the card I would like to see our motto "Built on integrity... Inspired by commitment." Consider adding a splash of bright orange to the card to complement the blues and silvers/grays in the logo. We are open to metallic inks, textures, etc. We would like to see options on both light and dark backgrounds. The font in the logo is Euro Technic Extended Regular.

```html
<!DOCTYPE html>
<html lang="en">
<head>
<meta charset="utf-8">
<title>Halden Contracting – Business Card</title>
<link href="https://fonts.googleapis.com/css2?family=Michroma&family=Questrial&display=swap" rel="stylesheet">
<style>
  :root {
    --stage: #2b2b2d;
    --blue-light: #1d72c8;
    --blue-deep: #2a46a3;
    --brand-blue: #2159b5;
    --ink-grey: #4a4a4f;
    --paper: #ffffff;
    --rule: #2f6fc2;
  }
  * { box-sizing: border-box; margin: 0; padding: 0; }
  html, body {
    width: 1200px; height: 800px; overflow: hidden;
    background: var(--stage);
  }
  .stage {
    position: relative; width: 1200px; height: 800px;
    display: flex; flex-direction: column; align-items: center; justify-content: center; gap: 40px;
  }
  .card {
    position: relative; width: 595px; height: 340px;
    box-shadow: 0 10px 30px rgba(0,0,0,.45);
  }
  /* Front */
  .card-front {
    background: linear-gradient(160deg, var(--blue-light) 0%, var(--blue-deep) 100%);
    color: var(--paper);
  }
  .front-brand {
    position: absolute; top: 120px; left: 0; right: 0; text-align: center;
    font-family: "Michroma", sans-serif; color: var(--paper);
    font-size: 40px; letter-spacing: 3px; line-height: 1;
  }
  .front-brand .brand-sub {
    display: block; font-size: 13px; letter-spacing: 2px; margin-top: 10px;
  }
  .motto {
    position: absolute; bottom: 36px; left: 0; right: 0; text-align: center;
    font-family: "Michroma", sans-serif; font-size: 11px; letter-spacing: 1.5px;
    color: var(--paper);
  }
  /* Back */
  .card-back { background: var(--paper); }
  .back-brand {
    position: absolute; top: 46px; right: 44px; text-align: right;
    font-family: "Michroma", sans-serif; color: var(--brand-blue);
    font-size: 28px; letter-spacing: 2px; line-height: 1;
  }
  .back-brand .brand-sub { display: block; font-size: 9px; letter-spacing: 1.5px; margin-top: 8px; }
  .divider {
    position: absolute; top: 150px; left: 40px; right: 40px; height: 1.5px; background: var(--rule);
  }
  .person { position: absolute; top: 172px; left: 40px; }
  .person-name {
    font-family: "Michroma", sans-serif; color: var(--brand-blue);
    font-size: 19px; letter-spacing: 1px;
  }
  .person-title {
    font-family: "Michroma", sans-serif; color: var(--ink-grey);
    font-size: 11px; letter-spacing: 1px; margin-top: 4px;
  }
  .person-rule { width: 150px; height: 1px; background: var(--rule); margin-top: 14px; }
  .contact { list-style: none; margin-top: 10px; }
  .contact li {
    display: flex; align-items: center; gap: 10px;
    font-family: "Michroma", sans-serif; font-size: 10.5px; color: var(--ink-grey);
    letter-spacing: .6px; line-height: 20px;
  }
  .contact svg { width: 11px; height: 11px; flex: none; }
  .contact .web-accent { color: var(--brand-blue); }
  .address {
    position: absolute; top: 176px; right: 44px; text-align: right;
    font-family: "Michroma", sans-serif; font-size: 10.5px; line-height: 17px;
    color: var(--ink-grey); letter-spacing: .6px;
  }
</style>
</head>
<body>
<main class="stage">
  <section class="card card-front">
    <div class="front-brand">HALDEN<span class="brand-sub">CONTRACTING, INC.</span></div>
    <p class="motto">“Built on integrity... Inspired by commitment.”</p>
  </section>

  <section class="card card-back">
    <div class="back-brand">HALDEN<span class="brand-sub">CONTRACTING, INC.</span></div>
    <div class="divider"></div>
    <div class="person">
      <h1 class="person-name">DANIEL BROOKS</h1>
      <p class="person-title">Ceo &amp; Founder</p>
      <div class="person-rule"></div>
      <ul class="contact">
        <li>
          <svg viewBox="0 0 12 12" aria-hidden="true"><path d="M2.5 1 L4.5 1 L5.2 3.5 L4 4.5 Q5 7 7.5 8 L8.5 6.8 L11 7.5 L11 9.5 Q10 11 8 10.8 Q2 9 1.2 3 Q1.2 1.6 2.5 1 Z" fill="#2159b5"/></svg>
          000 111 2223
        </li>
        <li>
          <svg viewBox="0 0 12 12" aria-hidden="true"><rect x="1" y="2.5" width="10" height="7" fill="none" stroke="#2159b5" stroke-width="1.2"/><path d="M1 2.5 L6 6.5 L11 2.5" fill="none" stroke="#2159b5" stroke-width="1.2"/></svg>
          urname@email.com
        </li>
        <li>
          <svg viewBox="0 0 12 12" aria-hidden="true"><circle cx="6" cy="6" r="5" fill="#2159b5"/><path d="M1 6 H11 M6 1 Q3 6 6 11 M6 1 Q9 6 6 11" fill="none" stroke="#fff" stroke-width=".8"/></svg>
          <span>www.<span class="web-accent">ursitename</span>.com</span>
        </li>
      </ul>
    </div>
    <address class="address" style="font-style:normal">Your Street Address,<br>UnitedStates, 1234</address>
  </section>
</main>
</body>
</html>
```